Small Business Broker Business Card Design

A business card design for a small business brokerage, which is a financial service, not unlike real estate brokerage, but for small businesses such as laundromats, pizza shops, restaurants, cleaners etc. The designs should all be simple, more conservative in nature, using the colors and font of the logo. Again, think real estate Brokerage as a business context
Contact Information for Business Card
Name: Glen R. Harlow. Title: Small Business Advisor. Email: g.harlow@bayfieldcapitalworks.example. Mobile: (555) 274-3918. Office: (555) 806-2147. www.bayfieldcapitalworks.example

```html
<!DOCTYPE html>
<html lang="en">
<head>
<meta charset="utf-8">
<title>Bayfield Capital Works – Business Card</title>
<link href="https://fonts.googleapis.com/css2?family=Montserrat:wght@400;500;600;700&display=swap" rel="stylesheet">
<style>
  :root{
    --navy:#1b3566;
    --green:#7ac143;
    --ink:#1c1c1c;
    --paper:#ffffff;
    --backdrop:#d9dadb;
  }
  *{box-sizing:border-box;margin:0;padding:0}
  html,body{width:1093px;height:1200px;overflow:hidden}
  body{background:var(--backdrop);position:relative;font-family:"Montserrat",sans-serif}
  .card{position:absolute;left:265px;width:580px;height:363px;border-radius:18px;overflow:hidden}
  .card--front{top:225px;background:var(--paper)}
  .card--back{top:615px;background:var(--navy)}

  .brand{position:absolute;text-align:center}
  .brand__mark{display:block;margin:0 auto}
  .brand__name{font-weight:700;letter-spacing:.2px;white-space:nowrap}
  .brand__tagline{color:var(--green);font-weight:600;white-space:nowrap;text-transform:uppercase}

  .card--front .brand{left:20px;width:242px;top:133px}
  .card--front .brand__mark{background:var(--navy);width:56px;height:56px;margin-bottom:13px}
  .card--front .brand__name{color:var(--navy);font-size:12.8px;line-height:1.1}
  .card--front .brand__tagline{font-size:6.4px;letter-spacing:1.1px;margin-top:3px}

  .divider{position:absolute;left:271px;top:116px;width:1.5px;height:148px;background:var(--navy)}

  .person{position:absolute;left:282px;top:111px}
  .person__name{color:var(--navy);font-weight:700;font-size:22px;line-height:1.2}
  .person__title{color:var(--ink);font-size:12.6px;font-weight:500;margin-top:1px}

  .contacts{position:absolute;left:284px;top:186px;list-style:none}
  .contacts li{display:flex;align-items:center;height:19.5px;font-size:12.6px;color:var(--ink);white-space:nowrap}
  .contacts li:nth-child(2){margin-top:5px}
  .contacts svg{width:12px;height:12px;margin-right:9px;fill:var(--navy);flex:none}

  .texture{position:absolute;inset:0;background:linear-gradient(215deg,rgba(120,150,200,.35) 0%,rgba(27,53,102,0) 45%),var(--navy)}
  .card--back .brand{left:0;right:0;top:205px}
  .card--back .brand__mark{background:var(--paper);width:48px;height:48px;margin-bottom:14px}
  .card--back .brand__name{color:var(--paper);font-size:19.5px;font-weight:600}
  .card--back .brand__tagline{font-size:9.8px;letter-spacing:1.2px;margin-top:3px}
</style>
</head>
<body>
  <section class="card card--front">
    <div class="brand">
      <span class="brand__mark"></span>
      <div class="brand__name">BAYFIELD CAPITAL WORKS, INC</div>
      <div class="brand__tagline">Trusted guidance to buy or sell your business</div>
    </div>
    <div class="divider"></div>
    <div class="person">
      <h1 class="person__name">Glen R. Harlow</h1>
      <p class="person__title">Small Business Advisor</p>
    </div>
    <ul class="contacts">
      <li><svg viewBox="0 0 24 24"><path d="M2 9c0-3 5-5 10-5s10 2 10 5v2h-5V9c-1-1-9-1-10 0v2H2z M6 12h12l3 7H3z"/></svg>(555) 806-2147</li>
      <li><svg viewBox="0 0 24 24"><path d="M6.6 10.8a15 15 0 0 0 6.6 6.6l2.2-2.2c.3-.3.7-.4 1-.2 1.1.4 2.3.6 3.6.6.6 0 1 .4 1 1V20c0 .6-.4 1-1 1A17 17 0 0 1 3 4c0-.6.4-1 1-1h3.5c.6 0 1 .4 1 1 0 1.3.2 2.5.6 3.6.1.3 0 .7-.2 1z"/></svg>(555) 274-3918</li>
      <li><svg viewBox="0 0 24 24"><path d="M2 5h20v2l-10 6L2 7z M2 9l10 6 10-6v10H2z"/></svg>g.harlow@bayfieldcapitalworks.example</li>
      <li><svg viewBox="0 0 24 24"><circle cx="12" cy="12" r="10"/><path d="M7 6c2 1 2 3 4 3s1 3 3 3 2 3 0 5" stroke="#fff" stroke-width="2" fill="none"/></svg>www.bayfieldcapitalworks.example</li>
    </ul>
  </section>

  <section class="card card--back">
    <div class="texture" role="img" aria-label="Faint repeating brand pattern across the navy background"></div>
    <div class="brand">
      <span class="brand__mark"></span>
      <div class="brand__name">BAYFIELD CAPITAL WORKS, INC</div>
      <div class="brand__tagline">Trusted guidance to buy or sell your business</div>
    </div>
  </section>
</body>
</html>
```